Redesign for a start up airline technology. The website is quelbrion.com.

I need a PowerPoint template that complements our website. I can provide our current template as a starting point.

```html
<!DOCTYPE html>
<html lang="en">
<head>
<meta charset="utf-8">
<title>Quelbrion Presentation Template</title>
<link href="https://fonts.googleapis.com/css2?family=Fira+Sans:wght@500;600;700&family=Source+Sans+3:wght@400;600&display=swap" rel="stylesheet">
<style>
:root{
  --canvas:#4a4a4b;
  --navy:#0a4a9c;
  --blue:#0b63c4;
  --sky:#1fa3e8;
  --green:#55b52c;
  --green-dark:#3f9a1f;
  --ink:#1d2430;
  --muted:#4b515b;
  --paper:#f3f4f6;
  --charcoal:#2b2b2c;
}
*{margin:0;padding:0;box-sizing:border-box}
html,body{width:1200px;height:712px;overflow:hidden;background:var(--canvas)}
body{position:relative;font-family:"Source Sans 3",sans-serif;color:var(--ink)}
.slide{position:absolute;width:378px;height:212px;overflow:hidden;background:var(--paper)}
.c1{left:18px}.c2{left:411px}.c3{left:805px}
.r1{top:19px}.r2{top:245px}.r3{top:468px}

.band{position:absolute;left:0;top:0;right:0;height:70px;background:linear-gradient(90deg,var(--navy),var(--blue) 55%,var(--sky))}
.sheet{position:absolute;left:0;right:0;top:34px;bottom:0;background:linear-gradient(150deg,#fbfbfc 0%,#eceef1 60%,#f6f7f8 100%);border-top-left-radius:44px 38px}
.band-title{position:absolute;left:27px;top:11px;font:600 8.6px "Fira Sans",sans-serif;color:#fff;letter-spacing:.3px;text-transform:uppercase}
.brand{position:absolute;right:14px;top:11px;font:700 8.4px "Fira Sans",sans-serif;color:#fff}
.pg{position:absolute;right:13px;bottom:9px;width:9px;height:9px;border-radius:50%;background:var(--green);color:#123;font:600 3.8px "Fira Sans",sans-serif;display:flex;align-items:center;justify-content:center}

.photo{position:absolute;border-radius:6px}
.h2{font:600 11px/1.3 "Fira Sans",sans-serif;color:var(--navy)}
.h2 b{color:var(--blue);font-weight:600}
.copy{font-size:4.6px;line-height:1.65;color:var(--muted)}

/* cover */
.cover{background:radial-gradient(circle at 50% 45%,#333334,var(--charcoal))}
.cover .brand-big{position:absolute;left:0;right:0;top:88px;text-align:center;font:700 34px "Fira Sans",sans-serif;color:var(--blue)}

/* welcome */
.welcome .hero{left:0;top:0;width:378px;height:170px;border-radius:0;background:linear-gradient(135deg,#16243a,#1d3e66 45%,#2a5d8f 70%,#121d2e)}
.welcome svg{position:absolute;left:0;top:0}
.welcome .badge{position:absolute;left:241px;top:112px;width:78px;height:78px;border-radius:50%;background:radial-gradient(circle at 40% 35%,var(--sky),var(--blue) 70%);border:3px solid #fff;display:flex;align-items:center;justify-content:center;font:700 9px "Fira Sans",sans-serif;color:#fff}
.welcome .title{position:absolute;left:21px;top:156px;font:600 12.6px "Fira Sans",sans-serif;color:#2a2d33}
.welcome .title span{color:var(--blue)}
.welcome .copy{position:absolute;left:22px;top:174px;width:210px;font-size:3.9px;line-height:1.9;color:#333}

/* contents */
.contents{background:linear-gradient(140deg,#fbfbfc,#eceef1)}
.contents svg{position:absolute;left:0;top:0}
.toc-title{position:absolute;left:56px;top:106px;transform:translate(-50%,-50%) rotate(-90deg);font:600 13px "Fira Sans",sans-serif;color:#fff;white-space:nowrap}
.toc{position:absolute;left:109px;top:29px;list-style:none}
.toc li{display:flex;align-items:center;height:23.2px;font:600 5.2px "Fira Sans",sans-serif;color:#222;letter-spacing:.2px}
.toc li i{width:13px;height:13px;border-radius:50%;border:2px solid #d8ecd0;background:var(--green);color:#fff;font:600 5px "Fira Sans",sans-serif;font-style:normal;display:flex;align-items:center;justify-content:center;margin-right:9px}
.contents .brand{color:var(--blue);top:12px}

/* overview */
.offset{position:absolute;background:var(--green);border-radius:5px}
.ov .offset{left:27px;top:54px;width:72px;height:80px}
.ov .map{left:35px;top:61px;width:127px;height:130px;background:radial-gradient(circle at 45% 45%,#6b4a1d,#1b2231 55%,#0a111c)}
.ov .h2{position:absolute;left:188px;top:67px;width:160px}
.ov .copy{position:absolute;left:188px;top:123px;width:140px}

/* about */
.about .h2{position:absolute;left:28px;top:51px;font-size:11px}
.about .left{position:absolute;left:28px;top:70px;width:134px}
.about .left p{margin-bottom:3px}
.about .right{position:absolute;left:189px;top:52px;width:176px}
.about .plan{left:189px;top:106px;width:87px;height:84px;border-radius:0;background:linear-gradient(160deg,#0b1420,#07101a)}
.about .hangar{left:278px;top:106px;width:87px;height:84px;border-radius:0;background:linear-gradient(170deg,#c9d3de,#9aa7b4 55%,#6d7682)}

/* leadership */
.lead .h2{position:absolute;left:28px;top:45px}
.card{position:absolute;width:108px;height:60px;background:#fff;border-radius:3px;box-shadow:0 1px 3px rgba(0,0,0,.12)}
.card .face{position:absolute;left:2px;top:2px;width:46px;height:56px;border-radius:2px;background:linear-gradient(180deg,#c9ced5,#7d8794)}
.card .info{position:absolute;left:53px;top:5px;width:52px}
.card .name{font:600 5.2px "Fira Sans",sans-serif;color:var(--blue)}
.card .role{font:600 3px "Fira Sans",sans-serif;color:var(--green-dark);text-transform:uppercase;margin:1px 0 2px;line-height:1.35}
.card .bio{font-size:3.4px;line-height:1.5;color:#444}

/* serve */
.tile{position:absolute;top:49px;width:111px;height:136px;border-radius:4px;padding:2px}
.tile .pic{position:relative;height:65px;border-radius:3px}
.tile h3{font:600 6.4px "Fira Sans",sans-serif;color:#fff;margin:7px 5px 3px}
.tile p{font-size:3.9px;line-height:1.75;color:#eaf4ff;margin:0 5px}
.t1{left:18px;background:var(--green-dark)}
.t2{left:135px;background:var(--blue)}
.t3{left:252px;background:var(--sky)}
.t1 .pic{background:linear-gradient(180deg,#7d6fa8,#d79ab8 55%,#e6c9d8)}
.t2 .pic{background:linear-gradient(180deg,#8aa0b8,#d6dbe1 60%,#f0ece6)}
.t3 .pic{background:linear-gradient(180deg,#c9a367,#e0c89a 55%,#b9a58a)}

/* system */
.sys .h2{position:absolute;left:36px;top:74px;width:130px;font-size:11px}
.sys ul{position:absolute;left:36px;top:125px;list-style:none;font:600 5.4px "Fira Sans",sans-serif;color:#1b2a44}
.sys li{margin-bottom:6px}
.sys li::before{content:"+";margin-right:4px}
.sys .offset{left:203px;top:52px;width:72px;height:130px}
.sys .gear{left:211px;top:59px;width:127px;height:129px;background:radial-gradient(circle at 55% 65%,#1b2c4a,#05070b 60%)}

/* contact */
.contact .scene{left:0;top:34px;width:378px;height:178px;border-radius:0;background:linear-gradient(100deg,#2b3a2a,#4f6240 40%,#6f7a5a 70%,#3c4633)}
.glass{position:absolute;left:26px;top:47px;width:144px;height:152px;border-radius:12px;background:rgba(25,28,30,.78)}
.row{position:absolute;left:9px;display:flex;gap:8px}
.row .ico{width:20px;height:20px;border-radius:50%;background:var(--green);border:2px solid #9fd27f;display:flex;align-items:center;justify-content:center;flex:none}
.row h4{font:600 10px "Fira Sans",sans-serif;color:#fff;margin-bottom:3px}
.row p{font-size:5px;line-height:1.8;color:#f1f1f1}
</style>
</head>
<body>

<section class="slide cover c1 r1">
  <div class="brand-big">Quelbrion</div>
</section>

<section class="slide welcome c2 r1">
  <div class="photo hero" role="img" aria-label="Photo of two engineers with a tablet beside a holographic aircraft model in a lab"></div>
  <svg width="378" height="212" viewBox="0 0 378 212">
    <path d="M0 137 C60 118 120 118 200 150 C260 172 320 150 378 128 L378 212 L0 212Z" fill="#8cc63f"/>
    <path d="M0 144 C60 126 120 126 200 157 C260 178 320 158 378 137 L378 212 L0 212Z" fill="#f7f8f9"/>
  </svg>
  <div class="badge">Quelbrion</div>
  <div class="title">WELCOME TO <span>QUELBRION</span></div>
  <p class="copy">Quelbrion is an aerospace technology company that produces a game changing onboard weight and balance measurement system - the Gear Load Sensing System (GLSS).<br>The GLSS hardware kit automatically calculates an aircraft's weight and center of gravity for each flight.</p>
  <div class="pg">02</div>
</section>

<section class="slide contents c3 r1">
  <svg width="378" height="212" viewBox="0 0 378 212">
    <defs><linearGradient id="tocBlue" x1="0" y1="0" x2="0" y2="1"><stop offset="0" stop-color="#0b5fc0"/><stop offset="1" stop-color="#0a4a9c"/></linearGradient></defs>
    <path d="M0 0 H143 Q117 18 117 70 V212 H0Z" fill="url(#tocBlue)"/>
  </svg>
  <div class="toc-title">TABLE OF CONTENTS</div>
  <div class="brand">Quelbrion</div>
  <ol class="toc">
    <li><i>1</i>PROJECT OVERVIEW</li>
    <li><i>2</i>WHO WE SERVE</li>
    <li><i>3</i>THE GEAR LOAD SENSING SYSTEM</li>
    <li><i>4</i>WHO WE ARE</li>
    <li><i>5</i>SUSTAINABILITY</li>
    <li><i>6</i>NEWS</li>
    <li><i>7</i>CONTACT US</li>
  </ol>
  <div class="pg">03</div>
</section>

<section class="slide ov c1 r2">
  <div class="band"></div><div class="sheet"></div>
  <div class="band-title">Project Overview</div>
  <div class="brand">Quelbrion</div>
  <div class="offset"></div>
  <div class="photo map" role="img" aria-label="Night satellite view of Europe with flight route lines"></div>
  <h2 class="h2">Unlocking the Future of Airline Operations and the Flying Experience</h2>
  <p class="copy">Quelbrion is an aerospace technology company that produces a game changing onboard weight and balance measurement system - the Gear Load Sensing System (GLSS). The GLSS hardware kit automatically calculates an aircraft's weight and center of gravity for each flight.</p>
  <div class="pg">04</div>
</section>

<section class="slide about c2 r2">
  <div class="band"></div><div class="sheet"></div>
  <div class="band-title">Who We Are</div>
  <div class="brand">Quelbrion</div>
  <h2 class="h2">About <b>Quelbrion</b></h2>
  <div class="left copy">
    <p>Quelbrion is an aerospace technology company that produces a game changing onboard weight and balance measurement system - the Gear Load Sensing System (GLSS). The GLSS hardware kit automatically calculates an aircraft's weight and center of gravity for each flight.</p>
    <p>With numerous design, process and method patents, Quelbrion brings a unique combination of engineering innovation and certification expertise within the airline and aerospace industries.</p>
    <p>The Quelbrion leadership team holds decades of airline and relevant aviation experience, including a FAA delegated authority in the areas of Electrical Systems and Certification Management as a Designated Engineering Representative (DER).</p>
  </div>
  <p class="right copy">The Gear Load Sensing System (GLSS) is the only commercially available onboard weight and balance measurement system that can automatically calculate an aircraft's weight and center of gravity for each flight. This innovative approach to weight and balance planning turns estimations into actuals that can maximize aircraft performance by optimizing load planning for more efficient flights.</p>
  <div class="photo plan" role="img" aria-label="Blueprint outline of an airliner with weight readings"></div>
  <div class="photo hangar" role="img" aria-label="Aircraft under maintenance in a bright hangar"></div>
  <div class="pg">05</div>
</section>

<section class="slide lead c3 r2">
  <div class="band"></div><div class="sheet"></div>
  <div class="band-title">Who We Are</div>
  <div class="brand">Quelbrion</div>
  <h2 class="h2">Quelbrion <b>Leadership</b></h2>
  <div class="card" style="left:28px;top:66px"><div class="face" role="img" aria-label="Portrait of the founder"></div><div class="info"><div class="name">Warren Ostby</div><div class="role">Founder and Senior Technical Fellow</div><div class="bio">Warren Ostby is the inventor of Quelbrion's inaugural product, the Gear Load Sensing System.</div></div></div>
  <div class="card" style="left:142px;top:66px"><div class="face" role="img" aria-label="Portrait of the CEO"></div><div class="info"><div class="name">Dean Carrow</div><div class="role">CEO</div><div class="bio">Dean Carrow is responsible for broadening and accelerating the industry's adoption of Quelbrion's Gear Load Sensing System (GLSS).</div></div></div>
  <div class="card" style="left:256px;top:66px"><div class="face" role="img" aria-label="Portrait of the chief operating officer"></div><div class="info"><div class="name">Lyle Pemberton</div><div class="bio">Lyle Pemberton is the chief operating officer of Quelbrion responsible for driving the development and implementation of commercial and operational strategies.</div></div></div>
  <div class="card" style="left:78px;top:131px"><div class="face" role="img" aria-label="Portrait of the CIO"></div><div class="info"><div class="name">Ravi Menon</div><div class="role">CIO</div><div class="bio">Ravi Menon is responsible for leading Quelbrion's technology strategy, overseeing technology operations, including architecture, infrastructure.</div></div></div>
  <div class="card" style="left:192px;top:131px"><div class="face" role="img" aria-label="Portrait of the head of engineering"></div><div class="info"><div class="name">Tom Hadley</div><div class="role">Head of Engineering</div><div class="bio">Tom Hadley is responsible for leading the design, certification, and deployment planning processes.</div></div></div>
  <div class="pg">06</div>
</section>

<section class="slide serve c1 r3">
  <div class="band"></div><div class="sheet"></div>
  <div class="band-title" style="left:18px">Who We Serve</div>
  <div class="brand">Quelbrion</div>
  <article class="tile t1"><div class="pic" role="img" aria-label="Airliner flying above pink sunset clouds"></div><h3>Commercial Aviation</h3><p>An innovative approach to weight and balance planning turns estimations into actuals. The Gear Load Sensing System unlocks the aircraft's untapped potential, optimizes load planning for more efficient flying and reduced fuel burn. GLSS technology provides continuous health monitoring for landing gear systems.</p></article>
  <article class="tile t2"><div class="pic" role="img" aria-label="Business jet flying over clouds"></div><h3>Regional and Business</h3><p>Accurate weight and loading data provides actionable information to get the most performance from your aircraft. An optimized center of gravity creates fuel efficiencies which can translate into increased payload and range. This data can also create efficiencies during the loading process, lowering operational costs and providing an increase return on investment.</p></article>
  <article class="tile t3"><div class="pic" role="img" aria-label="Fighter jet taking off over desert dust"></div><h3>Military</h3><p>Mission ready military aircraft are critical for success – humanitarian or war-fighting initiatives. A data-driven plan for efficient loading optimizing the center of gravity and leads to shortened time on the ground, reduced fuel burn and increased time over target.</p></article>
  <div class="pg">07</div>
</section>

<section class="slide sys c2 r3">
  <div class="band"></div><div class="sheet"></div>
  <div class="band-title" style="left:21px">The Gear Load Sensing System</div>
  <div class="brand">Quelbrion</div>
  <h2 class="h2">An automated onboard weightand balance measurement system</h2>
  <ul><li>27 Patents (Awarded and Pending)</li><li>Over 3,000 Commercial Flights</li></ul>
  <div class="offset"></div>
  <div class="photo gear" role="img" aria-label="Blueprint drawing of a landing gear strut and wheel on a grid"></div>
  <div class="pg">08</div>
</section>

<section class="slide contact c3 r3">
  <div class="band"></div>
  <div class="photo scene" role="img" aria-label="Hand launching a paper plane against a blurred forest"></div>
  <div class="band-title" style="left:21px">Contact Us</div>
  <div class="brand">Quelbrion</div>
  <div class="glass">
    <div class="row" style="top:24px"><span class="ico"><svg width="9" height="10" viewBox="0 0 9 10"><path d="M4.5 0.5a3.3 3.3 0 0 1 3.3 3.3c0 2.4-3.3 5.7-3.3 5.7S1.2 6.2 1.2 3.8A3.3 3.3 0 0 1 4.5 0.5z" fill="#153"/><circle cx="4.5" cy="3.8" r="1.2" fill="#9fd27f"/></svg></span><div><h4>Address:</h4><p>4170 Harlow Park Rd. Suite 220 Austin,<br>Texas 78701</p></div></div>
    <div class="row" style="top:68px"><span class="ico"><svg width="10" height="10" viewBox="0 0 10 10"><path d="M1 3.2C1 2 2.5 1 5 1s4 1 4 2.2L7.6 4 6.6 3H3.4L2.4 4zM2.6 5h4.8l.8 4H1.8z" fill="#153"/><circle cx="5" cy="6.8" r="1" fill="#9fd27f"/></svg></span><div><h4>Phone Number :</h4><p>+1 555 014 2290</p></div></div>
    <div class="row" style="top:104px"><span class="ico"><svg width="10" height="8" viewBox="0 0 10 8"><rect x="0.5" y="0.5" width="9" height="7" rx="1" fill="#153"/><path d="M1 1l4 3.4L9 1" stroke="#9fd27f" stroke-width="0.9" fill="none"/></svg></span><div><h4>Email :</h4><p>info@quelbrion.com</p></div></div>
  </div>
  <div class="pg">09</div>
</section>

</body>
</html>
```